Paint Retail Store needs a logo/label redesign.

We are redesigning a label for one of our products. We are a paint retail store that specializes on selling Quality Coatings, Everyday Value called Coat & Gleam. We want the redesign to exude professionalism and cleanliness. Attached is a picture of our current label. We want the logo Coat & Gleam to be modified to a more modern feel that still incorporates the iconic paint roller element that has been part of our brand identity. We want the description of: Exceptional Durability/ Luxurious Finish to be included in the front of the label to attract our clients. Include all of the information and description of the current label to the new label. Attached are pictures of our competitors labels so you have an idea of what we are looking for. We also want the background of the label to be a clean solid color.

Target Market(s)

Home Owners, DIY enthusiasts, Contractors/painters, interior designers

Industry/Entity Type

Paint and Coatings retail store

Colors

Designer to choose colors to be used in the design.

Requirements
Must have
• Semigloss Finish, Exceptional Durability, Luxurios Finish. Include all the information that are on the side of the current label to the new label. Include the phrase: Made in the US.
Nice to have
• A redesign of the logo: Coat & Gleam to convey a more modern/professional look.
Should not have
• Feminine colors.

```html
<!DOCTYPE html>
<html lang="en">
<head>
<meta charset="utf-8">
<title>Coat &amp; Gleam – Semi-Gloss Latex Paint Label</title>
<link href="https://fonts.googleapis.com/css2?family=Hind:wght@300;400;600;700&family=Cinzel:wght@500&family=Titan+One&family=Saira+Condensed:wght@400&display=swap" rel="stylesheet">
<style>
:root{
  --stage:#9c9ea2;
  --stage-light:#b4b6b9;
  --navy-deep:#14305c;
  --navy:#1d4384;
  --orange:#f08a24;
  --grey-bar:#8d8f93;
  --white:#ffffff;
}
*{box-sizing:border-box;margin:0;padding:0}
html,body{width:964px;height:1200px;overflow:hidden}
body{
  position:relative;
  background:radial-gradient(ellipse at 50% 45%,var(--stage-light),var(--stage) 75%);
  font-family:"Hind",sans-serif;color:var(--white);
}
.brand-header{position:absolute;left:26px;top:60px}
.brand-name{
  display:flex;align-items:center;gap:12px;
  font:700 50px/1 "Hind",sans-serif;color:var(--orange);
}
.brand-mark{width:20px;height:20px;background:var(--orange);flex:none}
.brand-tagline{margin-top:12px;font:400 19px/1 "Saira Condensed",sans-serif;color:var(--white);letter-spacing:.3px}

.label{
  position:absolute;left:32px;top:470px;width:900px;height:653px;
  background:linear-gradient(180deg,var(--navy-deep) 0%,var(--navy) 55%,var(--navy-deep) 100%);
  overflow:hidden;
}
.panel-left{position:absolute;left:36px;top:42px;width:214px;font-size:8.6px;line-height:1.28;text-align:justify}
.panel-left b{font-weight:700}
.ingredients{
  position:absolute;left:47px;top:496px;width:194px;height:146px;
  background:rgba(185,188,193,.28);border:1px solid rgba(255,255,255,.35);border-radius:6px;
  padding:10px 14px;font-size:7.4px;line-height:1.35;
}
.ingredients h4{font-weight:600;font-size:9.5px;margin-bottom:10px;display:flex;gap:22px}
.ingredients .row{display:flex;justify-content:space-between;border-bottom:1px dotted rgba(255,255,255,.4)}
.ingredients .note{margin-top:22px}

.panel-center{position:absolute;left:250px;top:0;width:400px;height:653px;text-align:center}
.finish-bar{
  position:absolute;left:91px;top:26px;width:218px;height:34px;background:var(--grey-bar);
  font:700 20px/36px "Hind",sans-serif;letter-spacing:1px;
}
.label-brand{
  position:absolute;left:0;right:0;top:125px;display:flex;justify-content:center;align-items:center;gap:10px;
  font:700 44px/1 "Hind",sans-serif;color:var(--orange);
}
.label-brand .brand-mark{width:18px;height:18px}
.label-tagline{position:absolute;left:0;right:0;top:238px;font:400 16px/1 "Saira Condensed",sans-serif}
.grade{position:absolute;left:0;right:0;top:296px;font:500 19px/1 "Cinzel",serif;color:var(--orange);letter-spacing:1px}
.claims{position:absolute;left:0;right:0;top:326px;font:300 23px/1.3 "Hind",sans-serif}
.claims .rule{width:90px;height:1px;background:var(--white);margin:0 auto}
.roller-art{
  position:absolute;left:60px;top:400px;width:290px;height:185px;
  background:linear-gradient(120deg,rgba(200,203,208,.85),rgba(160,164,170,.55));
  border-radius:6px 30px 10px 40px;
}
.product-type{position:absolute;left:0;right:0;top:478px;font:400 44px/1 "Titan One",sans-serif;color:var(--orange)}
.use{position:absolute;left:0;right:0;top:530px;font:700 18px/1 "Hind",sans-serif;letter-spacing:1px}
.badge{position:absolute;left:176px;top:564px;width:50px;height:50px;border-radius:50%;background:var(--white);border:3px solid #2f7fd6}
.volume{position:absolute;left:12px;top:596px;text-align:left;font:400 12.5px/1.3 "Hind",sans-serif}
.origin{position:absolute;left:300px;top:620px;font-size:8.5px;white-space:nowrap}

.panel-right{position:absolute;left:650px;top:42px;width:226px;font-size:8.4px;line-height:1.3}
.panel-right p{margin-bottom:10px}
.alert{color:var(--orange);font-weight:600}
.steps{border:1px solid rgba(255,255,255,.35);margin:4px 0 12px}
.steps-head{background:var(--orange);font-weight:700;font-size:8px;padding:2px 6px;width:72%}
.steps-grid{display:grid;grid-template-columns:repeat(3,1fr);gap:8px 10px;padding:8px}
.step-icon{width:34px;height:34px;background:var(--white);border-radius:2px}
.step-cap{font-size:6px;line-height:1.15;margin-top:3px}
</style>
</head>
<body>
  <header class="brand-header">
    <div class="brand-name"><span class="brand-mark"></span>Coat &amp; Gleam</div>
    <div class="brand-tagline">Quality Coatings, Everyday Value</div>
  </header>

  <section class="label">
    <div class="panel-left">
      <p><b>Where To Use:</b> Walls cabinets, ceilings, trim and doors. Use over drywall, wood, concrete/brick plaster and wallpaper. See bellow for preparation steps:</p>
      <p><b>How Much You Need:</b> For one coat coverage, apply at a maximum of 400 square feet per gallon. Rough or textured surfaces may require more allow for 125-300 square feet per gallon. Do not thin.</p>
      <p><b>What Tools To Use:</b> May be applied with a quality roller, a nylon/polyester brush, or a paint pad How To Apply Room and surface temperature must be 50 degrees Fahrenheit. Allow at least 4 hours of drying time before recoating. Mix gallons togheter for color and sheen uniformity when using more than one gallon of the same product</p>
      <p><b>Care for Freshly Painted Surfaces.</b> Freshly painted surfaced may be washed either 30 days- Until then avoid touching, wiping, or wetting the surface. Then clean with mild, non-abrasive, non-oily cleanser and water. Do not place objects on painted sirfaces untill throughly dry. Soap and Water Cleanup</p>
      <p><b>HOW TO PREPARE THE SURFACE</b><br>Previously Painted Surfaces: Remove loose paint, Wash with a mild, non-abrasive, non-oily cleanser and water. Rinse completely, let dry Patch holes and cracks with speckling paste and let dry. Sand patched area and wipe off residue. Send all smooth or glossy surfaces, rinse well. Unpainted Surfaces: Wallboard or brywall Concrete/brick Allow new masonry to sure at least 30 days Etch smooth unpainted concrete. Remove all loose concrete and efflorescence: Rinse and allow to dry Plaster (new) Must be died and cured for 30 days. Prime with primer. Let dry 4 hours before top coating. Wallpaper Vinyl coated wallpaper may be coated if all seams and edges are glued tight. Self-sand and wipe clean. Use primer and alllow 24 hours to dry.</p>
    </div>
    <div class="ingredients">
      <h4><span>CAS NO.</span><span>INGREDIENTS</span></h4>
      <div class="row"><span>7732-18-5</span><span>Water</span></div>
      <div class="row"><span>Propietary</span><span>Vinyl Polymer</span></div>
      <div class="row"><span>13463-67-7</span><span>Titanium Dioxide</span></div>
      <div class="row"><span>Proprietary</span><span>Acrylic Polymer</span></div>
      <div class="row"><span>471-34-1</span><span>Calcium Carbonate</span></div>
      <div class="row"><span>14464-46-1</span><span>Cristobalite</span></div>
      <div class="note">NON-PHOTOCHEMICALLY REACTIVE</div>
    </div>

    <div class="panel-center">
      <div class="finish-bar">SEMI - GLOSS</div>
      <div class="label-brand"><span class="brand-mark"></span>Coat &amp; Gleam</div>
      <div class="label-tagline">Quality Coatings, Everyday Value</div>
      <div class="grade">Premium Grade</div>
      <div class="claims">EXCEPTIONAL DURABILITY<div class="rule"></div>LUXURIOUS FINISH</div>
      <div class="roller-art" role="img" aria-label="Paint roller over a grey brush stroke"></div>
      <div class="product-type">Latex Paint</div>
      <div class="use">INTERIOR / EXTERIOR</div>
      <div class="badge" role="img" aria-label="Frozen product badge"></div>
      <div class="volume">1 Gal.<br>(124 OZ/3.667 Lts.)</div>
      <div class="origin">Made in the US.</div>
    </div>

    <div class="panel-right">
      <p class="alert">SOLID VINYL WALLPAPER CANNOT BE PAINTED</p>
      <p>CAUTIONS CONTAINS CRYSTALLINE SILICA- Use Cleanup: Clean tools, spills and splatters immediately with soap and water.</p>
      <div class="steps">
        <div class="steps-head">KEEP FROM FREEZING-DO NOT THIN</div>
        <div class="steps-grid">
          <div><div class="step-icon" role="img" aria-label="Clean surface icon"></div><div class="step-cap">Clean, dull and dry surface</div></div>
          <div><div class="step-icon" role="img" aria-label="Stir paint icon"></div><div class="step-cap">Stir paint thoroughly</div></div>
          <div><div class="step-icon" role="img" aria-label="Ceiling edge icon"></div><div class="step-cap">Start at ceiling edge</div></div>
          <div><div class="step-icon" role="img" aria-label="Roller pattern icon"></div><div class="step-cap">Paint "N" pattern fill in</div></div>
          <div><div class="step-icon" role="img" aria-label="Trim brush icon"></div><div class="step-cap">Paint trim last</div></div>
          <div><div class="step-icon" role="img" aria-label="Clean-up icon"></div><div class="step-cap">Soap and water clean-up</div></div>
        </div>
      </div>
      <p>only with adecuate ventilation To avoid overexposure, open windows and doors or use other means to ensure fresh air entry during aplication and drying. If you experience eye watering, headaches, or dizzyness, increase fresh air, or wear respiratory protection or leave the area. Adecuate ventilation required when sending or abrading the dried film. If adequate ventilation cannot ve provided wear an approved particulate respirator. Follow resporator manufacturer's directions for respirator use. Avoid contact with eyes and skin. Wash hands after using. Keep container closed when not in use Do not transfer contents to other containers for storage</p>
      <p>FIRST AID. In case of eye contact flush thoroughly with large amounts of water. Get medical attention if mation persists, fallowed, call Poison Control Center. hospital emergency room, or physician immediately</p>
      <p>DELAYED EFFECTS FROM LONG TERM OVEREXPOSURE Abrading on sanding of the dry film may release crystaline silica which has been shown to cause lung damage and cancer under long term expusurur</p>
      <p>WARNING: This product contains chemicals known to the State of California to cause cancer and birth defects or other reproductive ha</p>
      <p class="alert">DO NOT TAKE INTERNALLY<br>KEEP OUT OF THE REACH OF CHILDREN</p>
    </div>
  </section>
</body>
</html>
```